Brookvane Consulting Business Card Design

Business Card Design for Brookvane Consulting. Brookvane Consulting is a boutique consultancy based in Atlanta, GA., that specializes in marketing strategy, organization planning, and leadership development. We provide solutions for small businesses and startups as well as Vantage 300 companies.

http://brookvaneconsulting.com/

Target Market(s)

We provide solutions for small businesses and startups as well as Vantage 300 companies.

Industry/Entity Type

Consulting

Contact Information for Business Card

Two sided business card with priority on contact information, logo, tag line (Inspiration to Dream More, Do More, Become More)

Colors

Designer to choose colors to be used in the design.

Requirements
Must have
• contact information, logo, tag line (Inspiration to Dream More, Do More, Become More)
• Simple no over communication.
Nice to have
• I would like to see different placements of logo and creative use of both sides of the card
Should not have
• Do not put too much information on the card.

```html
<!DOCTYPE html>
<html lang="en">
<head>
<meta charset="utf-8">
<title>Brookvane Consulting – Business Card</title>
<link href="https://fonts.googleapis.com/css2?family=Lato:wght@400;700&display=swap" rel="stylesheet">
<style>
  :root {
    --backdrop: #3b3532;
    --card: #121212;
    --card-edge: #1c1c1c;
    --ink: #f2f2f2;
    --ink-soft: #cfcfcf;
    --rule: #6a6a6a;
    --foil: #c9c9c9;
  }
  * { margin: 0; padding: 0; box-sizing: border-box; }
  html, body {
    width: 1200px; height: 769px; overflow: hidden;
    background: var(--backdrop);
    font-family: "Lato", Arial, sans-serif;
  }
  .stage {
    position: relative; width: 1200px; height: 769px;
    display: flex; align-items: center; justify-content: center; gap: 50px;
  }
  .card {
    position: relative; width: 525px; height: 300px;
    background: var(--card);
    border: 1px solid var(--card-edge);
    box-shadow: 0 10px 30px rgba(0,0,0,.45);
    color: var(--ink);
  }
  /* Front: contact side */
  .brand {
    position: absolute; display: flex; align-items: center; gap: 10px;
    font-weight: 700; color: var(--ink); white-space: nowrap;
  }
  .brand-mark { width: 12px; height: 12px; background: var(--ink); }
  .front .brand { top: 62px; right: 70px; font-size: 26px; }
  .front .divider {
    position: absolute; top: 128px; left: 30px; right: 60px;
    height: 1px; background: var(--rule);
  }
  .tagline {
    position: absolute; top: 150px; right: 60px;
    text-align: right; font-size: 13px; line-height: 19px; color: var(--ink-soft);
  }
  .person { position: absolute; left: 40px; top: 176px; }
  .person-name { font-size: 17px; font-weight: 700; letter-spacing: .5px; color: var(--ink-soft); }
  .person-role { font-size: 13px; margin-top: 2px; color: var(--ink); }
  .person-rule { width: 200px; height: 1px; background: var(--rule); margin: 9px 0 8px; }
  .contact { list-style: none; font-size: 12.5px; color: var(--ink-soft); }
  .contact li { display: flex; align-items: center; gap: 9px; line-height: 19px; }
  .contact svg { width: 11px; height: 11px; fill: var(--ink-soft); flex: none; }
  /* Back: logo side */
  .back .brand {
    top: 50%; left: 50%; transform: translate(-50%, -50%);
    font-size: 34px; color: var(--foil);
  }
  .back .brand-mark { width: 16px; height: 16px; background: var(--foil); }
</style>
</head>
<body>
<main class="stage">
  <section class="card front" aria-label="Card front">
    <div class="brand"><span class="brand-mark"></span>Brookvane Consulting</div>
    <div class="divider"></div>
    <p class="tagline">Inspiration to Dream More<br>Do More, Become More</p>
    <div class="person">
      <p class="person-name">DANA WHITFIELD</p>
      <p class="person-role">Founder/Managing Director</p>
      <div class="person-rule"></div>
      <ul class="contact">
        <li><svg viewBox="0 0 16 16" aria-hidden="true"><path d="M3.5 1 6 4 4.5 6c1 2 3 4 5.5 5.5L12 10l3 2.5-1.5 2.5C8 15 1 8 1 2.5z"/></svg>555-010-2244</li>
        <li><svg viewBox="0 0 16 16" aria-hidden="true"><path d="M1 3h14v10H1zM2 4.2V5l6 4 6-4v-.8L8 8z" fill-rule="evenodd"/></svg>dana@brookvaneconsulting.com</li>
        <li><svg viewBox="0 0 16 16" aria-hidden="true"><circle cx="8" cy="8" r="7"/></svg>brookvaneconsulting.com</li>
      </ul>
    </div>
  </section>
  <section class="card back" aria-label="Card back">
    <div class="brand"><span class="brand-mark"></span>Brookvane Consulting</div>
  </section>
</main>
</body>
</html>
```